KORV PTY LTD - Business Cards

Design a modern business card - using the attached Designs.
Same design as on the front, apart from the names/numbers/emails to be different.
We want the cards to be very glossy to stand out, do I think the simple black/white/metallic will be effective.
Both lots of details below:

Tom Wrenshaw
Director
tom_korv@nulvane.com
0438 274 093

Lewis Corbyn
Director
lewis_korv@nulvane.com
0419 385 642

Industry/Entity Type

Business

```html
<!DOCTYPE html>
<html lang="en">
<head>
<meta charset="utf-8">
<title>KORV PTY LTD – Business Cards</title>
<link href="https://fonts.googleapis.com/css2?family=Noto+Serif:wght@400;700&display=swap" rel="stylesheet">
<style>
  :root {
    --backdrop: #e9e7e4;
    --card-white: #ffffff;
    --card-dark: #263039;
    --curve-grey: #c9cccf;
    --text-light: #ffffff;
    --mark-ink: #3a4149;
    --metal-light: #f4f5f6;
    --metal-mid: #c3c8cc;
    --metal-dark: #98a2a8;
  }
  * { margin: 0; padding: 0; box-sizing: border-box; }
  html, body {
    width: 1200px; height: 475px; overflow: hidden;
    background: var(--backdrop);
    font-family: "Noto Serif", Georgia, serif;
  }
  .canvas {
    position: relative; width: 1200px; height: 475px;
    display: flex; justify-content: center; align-items: center; gap: 40px;
  }
  .card {
    position: relative; width: 540px; height: 310px; overflow: hidden;
    box-shadow: 0 6px 18px rgba(0,0,0,.25);
  }
  .card-front { background: var(--card-white); }
  .front-panel { position: absolute; inset: 0; }
  .brand {
    position: absolute; display: flex; align-items: center; gap: 10px;
    color: var(--mark-ink); font-weight: 700;
  }
  .card-front .brand { left: 52px; top: 132px; font-size: 34px; }
  .brand-dot {
    width: 26px; height: 26px; border-radius: 50%; background: var(--mark-ink);
  }
  .details {
    position: absolute; left: 300px; top: 100px; color: var(--text-light);
  }
  .name { font-size: 22px; font-weight: 400; }
  .role { font-size: 13px; margin-top: 8px; margin-left: 6px; }
  .contact { list-style: none; margin-top: 34px; margin-left: 14px; font-size: 14px; }
  .contact li { display: flex; align-items: center; gap: 7px; margin-bottom: 6px; }
  .contact svg { width: 12px; height: 12px; fill: var(--text-light); }
  .card-back {
    background: linear-gradient(100deg, var(--metal-light) 0%, var(--metal-mid) 22%,
      var(--metal-light) 45%, var(--metal-light) 62%, var(--metal-mid) 82%, var(--metal-dark) 100%);
  }
  .card-back .brand {
    left: 50%; top: 50%; transform: translate(-50%, -50%); font-size: 64px; gap: 16px;
  }
  .card-back .brand-dot { width: 44px; height: 44px; }
</style>
</head>
<body>
<main class="canvas">
  <section class="card card-front" aria-label="Business card front">
    <svg class="front-panel" viewBox="0 0 540 310" preserveAspectRatio="none" aria-hidden="true">
      <path d="M262 0 C225 70 238 150 262 210 C280 255 282 290 270 310 L540 310 L540 0 Z" fill="var(--curve-grey)"/>
      <path d="M274 0 C237 70 250 150 274 210 C292 255 294 290 282 310 L540 310 L540 0 Z" fill="var(--card-dark)"/>
    </svg>
    <div class="brand"><span class="brand-dot"></span>KORV</div>
    <div class="details">
      <h1 class="name">Lewis Corbyn</h1>
      <p class="role">Director</p>
      <ul class="contact">
        <li>
          <svg viewBox="0 0 24 24"><path d="M6.6 10.8a15 15 0 0 0 6.6 6.6l2.2-2.2c.3-.3.7-.4 1-.2 1.1.4 2.3.6 3.6.6.6 0 1 .4 1 1V20c0 .6-.4 1-1 1A17 17 0 0 1 3 4c0-.6.4-1 1-1h3.5c.6 0 1 .4 1 1 0 1.3.2 2.5.6 3.6.1.3 0 .7-.2 1z"/></svg>
          0419 385 642
        </li>
        <li>
          <svg viewBox="0 0 24 24"><path d="M2 5h20v14H2z M2 5l10 8 10-8" /></svg>
          lewis_korv@nulvane.com
        </li>
      </ul>
    </div>
  </section>

  <section class="card card-back" aria-label="Business card back">
    <div class="brand"><span class="brand-dot"></span>KORV</div>
  </section>
</main>
</body>
</html>
```